Velmor Spire Nine Flash website

we need a website to cater to 2 aspect of the business. We have Velmor spire residence and velmor spire office. For the office, we will get their inquire and arrange a face to face meetup to show them the office area for rent. For the residence side, it will need to be like staylane or roomvio.com. we want to allow them to book online for the date they need. We have a total of 10 different room configurations starting at $70 per night and up depending on the size of the room. example of the design is https://brisquelodge.com/

Target Market(s)

the website should have detail information on the layout, designs, and luxury of the building.

Industry/Entity Type

office and service appartment rental/lease

Coding

Coded - Design and coding required

Number of Pages Required

5+ page

Requirements
Must have
• a luxury perspective
Nice to have
• example https://brisquelodge.com/

```html
<!DOCTYPE html>
<html lang="en">
<head>
<meta charset="utf-8">
<title>Velmor Spire Nine</title>
<link href="https://fonts.googleapis.com/css2?family=Cinzel:wght@400;500&family=Poppins:wght@300;400;500;600;700&display=swap" rel="stylesheet">
<style>
:root{
  --gold:#d39a2c;
  --gold-soft:#fbd98a;
  --cream:#fdeccb;
  --ink:#111111;
  --text:#777777;
  --white:#ffffff;
  --line:#e4e4e4;
}
*{box-sizing:border-box;margin:0;padding:0}
html,body{width:1200px;height:2191px;overflow:hidden;background:#fff}
body{font-family:'Poppins',sans-serif;color:var(--ink)}
a{text-decoration:none}
.stage{position:absolute;left:0;top:0;width:1411px;height:2576px;transform:scale(0.85046);transform-origin:0 0}
.abs{position:absolute}
.serif{font-family:'Cinzel',serif;font-weight:400}
.btn{position:absolute;display:flex;align-items:center;justify-content:center;border-radius:20px;font-size:10.5px;font-weight:700;text-transform:uppercase;letter-spacing:.2px}
.btn-gold{background:var(--gold);color:#fff}
.btn-white{background:#fff;color:var(--ink)}
.btn-soft{background:var(--gold-soft);color:var(--ink)}
.photo{position:absolute}

/* landing hero */
.landing{left:0;top:0;width:658px;height:341px;overflow:hidden}
.landing .photo{inset:0;background:linear-gradient(180deg,#8e9396 0%,#c9ccce 45%,#a7aaac 100%)}
.landing-name{left:0;width:658px;top:48px;text-align:center;color:#fff;font-size:14px}
.landing-title{left:0;width:658px;top:96px;text-align:center;color:#fff;font-size:37px;line-height:34px}
.landing-badge{left:305px;top:0;width:48px;height:44px;background:#fff;border-radius:0 0 24px 24px}

/* site */
.site{left:752px;top:0;width:659px;height:2576px;background:#fff;overflow:hidden}
.topbar{left:0;top:0;width:659px;height:28px;background:var(--gold)}
.topbar .phone{left:60px;top:7px;color:#fff;font-size:10px;display:flex;align-items:center;gap:6px}
.social{left:390px;top:7px;display:flex;gap:4px}
.social span{width:14px;height:14px;border-radius:50%;background:#fff}
.nav{left:0;top:28px;width:659px;height:59px;background:#fff;box-shadow:0 2px 6px rgba(0,0,0,.05)}
.nav a{position:absolute;top:24px;font-size:10px;color:var(--ink);transform:translateX(-50%)}
.nav-tab{left:270px;top:0;width:120px;height:116px}
.brand{left:230px;top:68px;width:200px;text-align:center;color:var(--gold);font-size:15px}
.hero{left:0;top:87px;width:659px;height:340px}
.hero .photo{inset:0;background:linear-gradient(120deg,#7a4a1c 0%,#b9893f 40%,#d9d2c4 65%,#7d98b4 100%)}
.hero h1{position:absolute;left:0;width:659px;top:112px;text-align:center;color:#fff;font-size:37px;line-height:35px;font-weight:400;font-family:'Cinzel',serif;text-shadow:0 2px 6px rgba(0,0,0,.3)}
.section-title{position:absolute;left:0;width:659px;text-align:center;font-size:21px;font-weight:400}
.about p{position:absolute;left:56px;width:547px;top:493px;text-align:center;font-size:9.6px;line-height:17px;color:var(--text)}
.offer{left:0;top:655px;width:659px;height:322px;background:var(--cream)}
.card{position:absolute;top:80px;width:174px;text-align:center}
.card .photo{position:relative;height:115px;background:linear-gradient(160deg,#c8b9a4,#eee7dc 55%,#8f8577)}
.card h3{font-family:'Cinzel',serif;font-weight:400;font-size:13px;margin-top:8px}
.card p{font-size:8.5px;line-height:11.5px;color:var(--text);margin:5px 6px 0}
.card .btn{position:relative;margin:11px auto 0;width:81px;height:23px;font-size:9px}
.rent-img{position:absolute;width:235px;height:176px;border-radius:7px;box-shadow:0 6px 16px rgba(0,0,0,.12)}
.rent-text{position:absolute;width:245px}
.rent-text h3{font-family:'Cinzel',serif;font-weight:400;font-size:18px}
.rent-text h4{font-size:10.5px;font-weight:500;margin-top:5px}
.rent-text p{font-size:8.5px;line-height:17px;color:var(--text);margin-top:6px}
.rent-text .btn{position:relative;margin-top:8px;width:85px;height:23px;font-size:9px}
.meetup{left:0;top:1730px;width:659px;height:258px}
.meetup .photo{inset:0;background:linear-gradient(100deg,#5b4a2e 0%,#b9a36e 30%,#d8d3cb 55%,#8e8f93 100%)}
.meetup h2{position:absolute;left:0;width:659px;top:98px;text-align:center;color:#fff;font-size:19px;font-family:'Cinzel',serif;font-weight:400}
.contact{left:62px;top:2022px;width:536px;height:326px;background:#fff;box-shadow:0 4px 18px rgba(0,0,0,.1)}
.field label{position:absolute;font-size:7px;color:var(--ink)}
.field .input{position:absolute;height:23px;border:1px solid var(--line);border-radius:3px;font-size:6.5px;color:#999;padding:8px 8px;display:flex;justify-content:space-between}
.field .input i{width:10px;height:10px;border:1px solid #aaa;border-radius:50%;margin-top:-2px}
.footer{left:0;top:2384px;width:659px;height:192px;background:var(--ink)}
.footer .brand-foot{left:0;width:659px;top:89px;text-align:center;color:var(--gold);font-size:19px}
.footer nav{position:absolute;left:0;width:659px;top:124px;display:flex;justify-content:center;font-size:9.5px;color:#fff}
.footer nav span{padding:0 16px;border-left:1px solid #fff;line-height:11px;color:#fff}
.footer nav span:first-child{border-left:none}
.footer hr{position:absolute;left:62px;width:536px;top:152px;border:none;border-top:1px solid #777}
.footer small{position:absolute;left:0;width:659px;top:167px;text-align:center;color:#fff;font-size:8px}
</style>
</head>
<body>
<div class="stage">

  <section class="abs landing">
    <div class="photo" role="img" aria-label="Bright open-plan office with rows of desks, chairs and plants"></div>
    <div class="abs landing-badge"></div>
    <div class="abs serif landing-name">Velmor Spire Nine</div>
    <h1 class="abs serif landing-title" style="font-weight:400">WELCOME<br>TO<br>VELMOR SPIRES</h1>
    <a class="btn btn-white" style="left:199px;top:214px;width:130px;height:26px;font-size:8.5px">Velmor Spire Residence</a>
    <a class="btn btn-gold" style="left:340px;top:214px;width:120px;height:26px;font-size:8.5px">Velmor Spire Office</a>
  </section>

  <main class="abs site">
    <div class="abs topbar">
      <div class="abs phone">
        <svg width="13" height="13" viewBox="0 0 24 24"><circle cx="12" cy="12" r="12" fill="#fff"/><path d="M8 6l2 0 1 3-1.5 1.2a8 8 0 0 0 4.3 4.3L15 13l3 1v2c0 1-1 2-2 2A10 10 0 0 1 6 8c0-1 1-2 2-2z" fill="#d39a2c"/></svg>
        +1(555) 014 2270
      </div>
      <div class="abs social"><span></span><span></span><span></span><span></span><span></span></div>
      <a class="btn btn-white" style="left:526px;top:5px;width:72px;height:18px;font-size:8.5px;color:var(--gold)">Book Now</a>
    </div>

    <nav class="abs nav">
      <a style="left:75px">Home</a>
      <a style="left:142px">About Us</a>
      <a style="left:223px">Our Serices</a>
      <a style="left:431px;top:23px">Testimonials</a>
      <a style="left:503px;top:23px">Blog</a>
      <a style="left:572px;top:23px">Contact Us</a>
    </nav>

    <section class="abs hero">
      <div class="photo" role="img" aria-label="Luxury boardroom with wooden slat wall and a city skyline view"></div>
      <h1>WELCOME TO<br>VELMOR SPIRES OFFICE.</h1>
      <a class="btn btn-gold" style="left:284px;top:200px;width:92px;height:24px;font-size:9px">Book Now</a>
    </section>

    <svg class="abs nav-tab" viewBox="0 0 120 116" aria-hidden="true"><path d="M0 28 L120 28 L120 60 Q120 90 60 116 Q0 90 0 60 Z" fill="#fff"/></svg>
    <div class="abs serif brand">Velmor Spire Nine</div>

    <section class="about">
      <h2 class="section-title serif" style="top:460px;color:var(--gold)">ABOUT US</h2>
      <p>"Lorem ipsum dolor sit amet, consectetur adipiscing elit, sed do eiusmod tempor incididunt ut labore et dolore magna aliqua. Ut enim ad minim veniam, quis nostrud exercitation ullamco laboris nisi ut aliquip ex ea commodo consequat. Duis aute irure dolor in reprehenderit in voluptate velit esse cillum dolore eu fugiat nulla pariatur. Excepteur sint occaecat cupidatat non proident, sunt in culpa qui officia deserunt mollit anim id est laborum."Sed ut perspiciatis unde omnis iste natus error sit voluptatem accusantium doloremque laudantium, totam rem</p>
      <a class="btn btn-gold" style="left:289px;top:593px;width:82px;height:24px;font-size:9px">Click Here</a>
    </section>

    <section class="abs offer">
      <h2 class="section-title serif" style="top:36px;font-size:19px">WHAT WE OFFER</h2>
      <div class="card" style="left:47px"><div class="photo" role="img" aria-label="Sunlit open office lounge"></div><h3>LOREM IPSUM</h3><p>Lorem ipsum dolor sit amet, consectetur adipiscing elit, sed do eiusmod tempor incididunt.</p><a class="btn btn-gold">Book Now</a></div>
      <div class="card" style="left:242px"><div class="photo" role="img" aria-label="Modern office interior with kitchenette and city view" style="background:linear-gradient(160deg,#555,#c9c6c0 55%,#8ca0a8)"></div><h3>LOREM IPSUM</h3><p>Lorem ipsum dolor sit amet, consectetur adipiscing elit, sed do eiusmod tempor incididunt.</p><a class="btn btn-gold">Book Now</a></div>
      <div class="card" style="left:439px"><div class="photo" role="img" aria-label="Curved reception lobby with warm lighting" style="background:linear-gradient(160deg,#e9e3da,#c8a57a 60%,#9c7a50)"></div><h3>LOREM IPSUM</h3><p>Lorem ipsum dolor sit amet, consectetur adipiscing elit, sed do eiusmod tempor incididunt.</p><a class="btn btn-gold">Book Now</a></div>
    </section>

    <section class="rent">
      <h2 class="section-title serif" style="top:1024px;color:var(--gold)">OFFICE AREA FOR RENT</h2>
      <div class="rent-img" role="img" aria-label="Modern office building exterior with parked cars" style="left:61px;top:1075px;background:linear-gradient(170deg,#7d8896,#a79a88 60%,#6c7a5c)"></div>
      <div class="rent-text" style="left:353px;top:1078px"><h3>LOREM IPSUM</h3><h4>LOREM IPSUM DOLOR SIT AMET,</h4><p>Lorem Ipsum is simply dummy text of the printing and typesetting industry. Lorem Ipsum has been the industry's standard dummy text ever since the 1500s, when an unknown printer took a galley of type and scrambled it to make a type specimen book.</p><a class="btn btn-soft">Book Now</a></div>

      <div class="rent-text" style="left:60px;top:1275px"><h3>LOREM IPSUM</h3><h4>LOREM IPSUM DOLOR SIT AMET,</h4><p>Lorem Ipsum is simply dummy text of the printing and typesetting industry. Lorem Ipsum has been the industry's standard dummy text ever since the 1500s, when an unknown printer took a galley of type and scrambled it to make a type specimen book.</p><a class="btn btn-soft">Book Now</a></div>
      <div class="rent-img" role="img" aria-label="Bright office room with desks and a glass chandelier" style="left:363px;top:1271px;background:linear-gradient(170deg,#5e6b78,#d8dadb 55%,#9ea3a6)"></div>

      <div class="rent-img" role="img" aria-label="Dark brick office block with planted frontage" style="left:61px;top:1468px;background:linear-gradient(170deg,#e9edf1,#3b3d42 40%,#55595c 80%,#6f7d52)"></div>
      <div class="rent-text" style="left:353px;top:1471px"><h3>LOREM IPSUM</h3><h4>LOREM IPSUM DOLOR SIT AMET,</h4><p>Lorem Ipsum is simply dummy text of the printing and typesetting industry. Lorem Ipsum has been the industry's standard dummy text ever since the 1500s, when an unknown printer took a galley of type and scrambled it to make a type specimen book.</p><a class="btn btn-soft">Book Now</a></div>

      <a class="btn btn-gold" style="left:284px;top:1668px;width:92px;height:23px;font-size:9px">View More</a>
    </section>

    <section class="abs meetup">
      <div class="photo" role="img" aria-label="Client meeting at a desk with an advisor reviewing paperwork"></div>
      <h2>FACE TO FACE MEETUP</h2>
      <a class="btn btn-white" style="left:288px;top:134px;width:84px;height:23px;font-size:9px">Click Here</a>
    </section>

    <section class="abs contact">
      <h2 class="section-title serif" style="left:0;width:536px;top:40px;color:var(--gold);font-size:20px">GET IN TOUCH WITH US</h2>
      <div class="field"><label style="left:20px;top:85px">Full Name</label><div class="input" style="left:20px;top:98px;width:232px">Lorem ipsum<i></i></div></div>
      <div class="field"><label style="left:284px;top:85px">E-mail</label><div class="input" style="left:284px;top:98px;width:232px">Lorem ipsum<i></i></div></div>
      <div class="field"><label style="left:20px;top:130px">Phone Number</label><div class="input" style="left:20px;top:143px;width:232px">+1(555) 014 2270<i></i></div></div>
      <div class="field"><label style="left:284px;top:130px">Date Of Birth</label><div class="input" style="left:284px;top:143px;width:232px">MM/dd/YY<i></i></div></div>
      <div class="field"><label style="left:20px;top:180px">Lorem ipsum dolor sit amet, consectetur.</label><div class="input" style="left:20px;top:194px;width:496px;height:37px">Message</div></div>
      <a class="btn btn-gold" style="left:20px;top:256px;width:92px;height:23px;font-size:9px">Send Message</a>
    </section>

    <footer class="abs footer">
      <div class="abs serif brand-foot">Velmor Spire Nine</div>
      <nav><span>Home</span><span>About Us</span><span>Our Serices</span><span>Testimonials</span><span>Blog</span><span>Contact Us</span></nav>
      <hr>
      <small>© Copyright by 2024 Velmor Spires.</small>
    </footer>
  </main>
</div>
</body>
</html>
```